New Website for World Wide Charity (KOLVAN)

We need a dynamic web design for our brand new charity organisation that will be working worldwide. We will be funded by donations so need to attract people to donate.

What We Do
We work to optimise the wellbeing of the planet, the animals and all that live within. Our slogan is Achieving Vibrational Equilibrium.

We have included a Powerpoint document which may help you understand what we need, it is just an idea for structure and style, it is not set in stone so feel free to be as creative as you like!
Updates

Designs look the same

Target Market(s)

Adults 18+ with an interest in animal, environmental. Businesses that may like to support our natural world or already support our natural world.

Number of Pages Required

3 page

Colors

Designer to choose colors to be used in the design.

Requirements
Must have
• We need the website to be easy to use and understand.

Web pages will be Home, What We Do, Who We Are, Success Stories, What You Can Do (Blog section), Seek Help, Donate, Join.
Nice to have
• Natural feel, easy to navigate, Ideally the website will look natural and organic.

Natural colours, blues, greens, sand, gold, brown, grey, silver, Orange and yellow for impact.
Should not have
• Should not have a dark coloured theme.

```html
<!DOCTYPE html>
<html lang="en">
<head>
<meta charset="utf-8">
<title>VERIDANE — Help Raise World Vibration</title>
<link rel="stylesheet" href="https://fonts.googleapis.com/css2?family=Roboto:wght@400;500;700&family=Arimo:wght@400;700&display=swap">
<style>
:root{
  --brand:#5b77b3;
  --brand-deep:#2c4a94;
  --ink:#222222;
  --ink-soft:#2b2b2b;
  --body:#777a80;
  --white:#ffffff;
  --sky-1:#2f6cc4;
  --sky-2:#7fa9e0;
  --snow-blue:#c9d8ee;
  --snow-shade:#7f98c0;
  --panel:rgba(91,119,179,.84);
}
*{margin:0;padding:0;box-sizing:border-box}
html,body{width:1200px;height:2902px;overflow:hidden;background:var(--white)}
body{position:relative;font-family:"Arimo",Arial,sans-serif;color:var(--ink)}
.abs{position:absolute}

/* hero */
.hero-bg{left:0;top:0;width:1200px;height:800px;
  background:
    radial-gradient(ellipse 380px 200px at 680px 230px,rgba(255,255,255,.55),rgba(255,255,255,0) 70%),
    radial-gradient(ellipse 700px 220px at 300px 330px,rgba(70,78,92,.35),rgba(70,78,92,0) 70%),
    radial-gradient(ellipse 520px 200px at 960px 380px,rgba(70,78,92,.32),rgba(70,78,92,0) 70%),
    linear-gradient(180deg,#8893aa 0%,#aab2c3 14%,#c6ccd7 24%,#9ea6b5 36%,#cfd3db 50%,#e6e8ec 62%,#b9bec8 78%,#c7cbd2 100%)}
.hero-curve{left:0;top:0}
.nav{top:52px;font-family:"Roboto",sans-serif;font-weight:700;font-size:14.5px;color:var(--ink-soft);display:flex;gap:23px;letter-spacing:.1px}
.nav-left{left:110px}
.nav-right{right:110px}
.nav .active{color:var(--brand-deep);position:relative}
.nav .active::after{content:"";position:absolute;left:0;right:0;top:22px;height:3px;background:var(--brand)}
.logo{border-radius:50%;display:flex;align-items:center;justify-content:center;gap:6px;
  font-family:"Roboto",sans-serif;font-weight:500;color:var(--brand);letter-spacing:.5px}
.logo-top{left:496px;top:13px;width:158px;height:158px;background:rgba(255,255,255,.85);border:2px solid var(--brand);font-size:18px}
.logo-mark{width:10px;height:10px;border-radius:50%;background:var(--brand);flex:none}
.hero-title{left:0;width:1200px;top:254px;text-align:center;font-family:"Roboto",sans-serif;font-weight:700;font-size:54px;color:var(--white);text-shadow:0 2px 6px rgba(0,0,0,.4)}
.btn{display:flex;align-items:center;justify-content:center;gap:6px;border-radius:26px;background:var(--brand);color:var(--white);font-family:"Roboto",sans-serif;font-weight:700;font-size:15px}
.hero-btn{left:498px;top:330px;width:205px;height:50px}

.pillar{border-radius:50%;display:flex;flex-direction:column;align-items:center;justify-content:center;color:var(--white);font-family:"Roboto",sans-serif;font-weight:700;box-shadow:0 10px 24px rgba(20,40,90,.35)}
.pillar-env{left:137px;top:536px;width:272px;height:272px;background:radial-gradient(circle at 50% 30%,#7ea17f,#5f8592 45%,#4a6a9e 75%,#3e5c9c);font-size:27px}
.pillar-hum{left:789px;top:536px;width:272px;height:272px;background:radial-gradient(circle at 45% 45%,#3c5ba0,#22397a 70%,#182d66);font-size:33px}
.pillar-ani{left:414px;top:486px;width:372px;height:372px;background:radial-gradient(circle at 50% 35%,#7a8fbd,#4b67aa 55%,#3553a0 85%);font-size:36px}
.ring{left:431px;top:503px;width:338px;height:338px;border-radius:50%;border:2px solid rgba(255,255,255,.85)}
.pillar .go{margin-top:48px;width:20px;height:20px}
.pillar-ani .find{margin-top:42px;width:178px;height:49px;border-radius:25px;background:rgba(120,140,190,.9);display:flex;align-items:center;justify-content:center;font-size:15px}

/* features */
.photo{border-radius:20px;width:471px;height:415px}
.photo-env{left:112px;top:924px;background:
  radial-gradient(ellipse 90px 60px at 330px 310px,rgba(200,140,90,.45),rgba(200,140,90,0) 70%),
  linear-gradient(180deg,#1c2c4c 0%,#2d4670 38%,#3a4f63 58%,#2a3a3c 66%,#c9d6e8 76%,#eef2f8 100%)}
.photo-ani{left:617px;top:1375px;background:
  radial-gradient(ellipse 150px 100px at 240px 210px,rgba(236,226,200,.85),rgba(236,226,200,0) 70%),
  linear-gradient(180deg,#b9c9d9 0%,#d7e0ea 48%,#c3d1df 62%,#e6ecf2 72%,#9fb3c8 100%)}
.photo-hum{left:112px;top:1825px;background:
  radial-gradient(ellipse 200px 170px at 240px 230px,#5b7a3a 0%,rgba(110,110,70,.7) 45%,rgba(150,110,90,0) 80%),
  linear-gradient(135deg,#8f6e5e 0%,#b48d7a 40%,#a47e6a 70%,#7d5c4c 100%)}
.feature{width:430px}
.feature h2{font-family:"Roboto",sans-serif;font-weight:700;font-size:41px;color:var(--ink);line-height:1}
.feature .rule{width:75px;height:4px;background:var(--brand);margin:16px 0 25px 3px}
.feature p{font-size:14.5px;line-height:22.4px;color:var(--body);text-align:justify;padding-left:3px}
.feature .btn{width:178px;height:49px;margin-top:34px}
.feat-env{left:633px;top:972px}
.feat-ani{left:135px;top:1423px}
.feat-hum{left:633px;top:1874px}
.arrow-ic{width:14px;height:14px}

/* footer */
.footer-bg{left:0;top:2300px;width:1200px;height:602px;background:
  radial-gradient(ellipse 500px 80px at 250px 2255px,rgba(255,255,255,0),rgba(255,255,255,0)),
  linear-gradient(180deg,var(--sky-1) 0%,var(--sky-2) 28%,#a9c4e8 38%,var(--snow-blue) 46%,#eef3f9 52%,#b7c8e2 62%,#9bb2d6 76%,var(--snow-shade) 100%)}
.footer-curve{left:0;top:2290px}
.logo-foot-ring{left:500px;top:2334px;width:200px;height:200px;border-radius:50%;background:var(--white)}
.logo-foot{left:520px;top:2354px;width:160px;height:160px;border:2px solid var(--brand);background:#f3eef4;font-size:18px}
.col{top:2552px;width:314px;height:267px;border-radius:20px;background:var(--panel);color:var(--white);padding:48px 0 0 47px}
.col h3{font-family:"Roboto",sans-serif;font-weight:500;font-size:22px;margin-bottom:22px}
.col ul{list-style:none}
.col li{font-size:15px;height:35.3px;display:flex;align-items:center;gap:12px}
.col li::before{content:"»";font-size:14px}
.col-1{left:110px}.col-2{left:444px}.col-3{left:777px}
.copyright{left:0;width:1200px;top:2849px;text-align:center;font-size:14.5px;color:var(--white);text-shadow:0 1px 3px rgba(30,50,90,.55)}
</style>
</head>
<body>

<header>
  <div class="abs hero-bg" role="img" aria-label="Snowy mountain landscape with pine forest under a cloudy sky"></div>
  <svg class="abs hero-curve" width="1200" height="800" viewBox="0 0 1200 800" aria-hidden="true">
    <path d="M0 770 Q600 560 1200 770 L1200 800 L0 800 Z" fill="#ffffff"/>
  </svg>

  <nav class="abs nav nav-left"><span class="active">HOME</span><span>WHAT WE DO</span><span>SUCCESS STORIES</span></nav>
  <nav class="abs nav nav-right"><span>WHO WE ARE</span><span>WHAT YOU CAN DO</span><span>DONATE</span><span>JOIN</span></nav>
  <div class="abs logo logo-top"><span class="logo-mark"></span>VERIDANE</div>

  <h1 class="abs hero-title">HELP RAISE WORLD VIBRATION</h1>
  <div class="abs btn hero-btn">MAKE A DIFFERENCE</div>

  <div class="abs pillar pillar-env" role="img" aria-label="Hands holding a small tree on grass">
    <span>ENVIRONMENT</span>
    <svg class="go" viewBox="0 0 20 20"><circle cx="10" cy="10" r="10" fill="#fff"/><path d="M8 5.5 L12.5 10 L8 14.5" stroke="#3b5b99" stroke-width="2.6" fill="none"/></svg>
  </div>
  <div class="abs pillar pillar-hum" role="img" aria-label="Network of connected people icons">
    <span>HUMAN</span>
    <svg class="go" viewBox="0 0 20 20"><circle cx="10" cy="10" r="10" fill="#fff"/><path d="M8 5.5 L12.5 10 L8 14.5" stroke="#1d3574" stroke-width="2.6" fill="none"/></svg>
  </div>
  <div class="abs pillar pillar-ani" role="img" aria-label="Polar bear on ice at dusk">
    <span style="margin-top:-8px">ANIMAL</span>
    <span class="find">FIND OUT MORE</span>
  </div>
  <div class="abs ring"></div>
</header>

<main>
  <div class="abs photo photo-env" role="img" aria-label="Snow-covered log cabin among pines under a starry sky"></div>
  <section class="abs feature feat-env">
    <h2>ENVIRONMENT</h2>
    <div class="rule"></div>
    <p>Lorem ipsum dolor sit amet, consectetur adipiscing elit, sed do eiusmod tempor incididunt ut labore et dolore magna aliqua. Ut enim ad minim veniam, quis nostrud exercitation ullamco laboris nisi ut aliquip ex ea commodo consequat. Duis aute irure dolor in reprehenderit in voluptate velit esse cillum dolore eu fugiat nulla pariatur. Excepteur sint occaecat cupidatat non proident, sunt in culpa qui officia deserunt mollit anim id est laborum.</p>
    <div class="btn">LEARN MORE <svg class="arrow-ic" viewBox="0 0 14 14"><circle cx="7" cy="7" r="7" fill="#fff"/><path d="M3.5 7 H9.5 M7 4.3 L9.8 7 L7 9.7" stroke="#5b77b3" stroke-width="1.8" fill="none"/></svg></div>
  </section>

  <section class="abs feature feat-ani">
    <h2>ANIMAL</h2>
    <div class="rule"></div>
    <p>Lorem ipsum dolor sit amet, consectetur adipiscing elit, sed do eiusmod tempor incididunt ut labore et dolore magna aliqua. Ut enim ad minim veniam, quis nostrud exercitation ullamco laboris nisi ut aliquip ex ea commodo consequat. Duis aute irure dolor in reprehenderit in voluptate velit esse cillum dolore eu fugiat nulla pariatur. Excepteur sint occaecat cupidatat non proident, sunt in culpa qui officia deserunt mollit anim id est laborum.</p>
    <div class="btn">LEARN MORE <svg class="arrow-ic" viewBox="0 0 14 14"><circle cx="7" cy="7" r="7" fill="#fff"/><path d="M3.5 7 H9.5 M7 4.3 L9.8 7 L7 9.7" stroke="#5b77b3" stroke-width="1.8" fill="none"/></svg></div>
  </section>
  <div class="abs photo photo-ani" role="img" aria-label="Polar bear standing on a floating ice block"></div>

  <div class="abs photo photo-hum" role="img" aria-label="Circle of joined hands over green grass"></div>
  <section class="abs feature feat-hum">
    <h2>HUMAN</h2>
    <div class="rule"></div>
    <p>Lorem ipsum dolor sit amet, consectetur adipiscing elit, sed do eiusmod tempor incididunt ut labore et dolore magna aliqua. Ut enim ad minim veniam, quis nostrud exercitation ullamco laboris nisi ut aliquip ex ea commodo consequat. Duis aute irure dolor in reprehenderit in voluptate velit esse cillum dolore eu fugiat nulla pariatur. Excepteur sint occaecat cupidatat non proident, sunt in culpa qui officia deserunt mollit anim id est laborum.</p>
    <div class="btn">LEARN MORE <svg class="arrow-ic" viewBox="0 0 14 14"><circle cx="7" cy="7" r="7" fill="#fff"/><path d="M3.5 7 H9.5 M7 4.3 L9.8 7 L7 9.7" stroke="#5b77b3" stroke-width="1.8" fill="none"/></svg></div>
  </section>
</main>

<footer>
  <div class="abs footer-bg" role="img" aria-label="Snowy mountain range under a bright blue sky"></div>
  <svg class="abs footer-curve" width="1200" height="200" viewBox="0 0 1200 200" aria-hidden="true">
    <path d="M0 0 L1200 0 L1200 18 Q600 240 0 18 Z" fill="#ffffff"/>
  </svg>
  <div class="abs logo-foot-ring"></div>
  <div class="abs logo logo-foot"><span class="logo-mark"></span>VERIDANE</div>

  <div class="abs col col-1">
    <h3>Get Involved</h3>
    <ul><li>Join Us</li><li>Fundraise</li><li>Donate</li><li>Shop</li></ul>
  </div>
  <div class="abs col col-2">
    <h3>Get Help</h3>
    <ul><li>Contact Us</li><li>Media</li></ul>
  </div>
  <div class="abs col col-3">
    <h3>Legal</h3>
    <ul><li>Terms and Conditions</li><li>Cookies</li><li>Privacy Policy</li></ul>
  </div>
  <p class="abs copyright">© Copyrights 2021 Company name | All Rights Reserved</p>
</footer>

</body>
</html>
```